Reach Crafters Unique Marketing Website Design

I am starting a new company that is a thought leader in the marketing consulting space. The company is called Reach Crafters. We intend to build a Wordpress site on the Astra Theme with the Spectra builder. Our goal is to become the leading voice that empowers high-ticket service business leaders to become Reach Crafters by equipping them with the cutting-edge frameworks and decision grade intelligence taught in leading business schools. What we are looking for is a website design that is clean and professional, making some use of white space well also being eye catching and distinctive in the consulting space. We will probably want to have a video on the homepage not in the hero section, but just below to explain the company and what we do. Our tagline is "Be found. Be chosen." I have attached a brand guide with some messaging, our typography choices, and our color system. The full site will have a primary nav that is four pages - About us, Services, Insights (essentially a blog), and Contact Us. The goal of this project is to develop an art direction that I can give to a designer to build loads of new pages.

Target Market(s)

Business owners (mostly male) from 30-60 years old, looking to fix their sales and marketing funnel.

Industry/Entity Type

Marketing consulting

Font styles to use
Sans Serif

Requirements
Must have
• A clean, professional design that builds trust with owners of high-ticket service businesses. We need a space for explainer video, and sections that tell prospects what we do. Would also like to have a blog carousel.
Nice to have
• Social feeds, if possible. See attached documents for colors and fonts.
Should not have
• Our feel is professional enough to be trustworthy, but unique enough to be memorable. Cartoon ideas do not meet the professional test, and we do not want the website to appear feminine.

```html
<!DOCTYPE html>
<html lang="en">
<head>
<meta charset="utf-8">
<title>Reach Crafters</title>
<link href="https://fonts.googleapis.com/css2?family=Bebas+Neue&family=Inter:wght@400;500;600;700&display=swap" rel="stylesheet">
<style>
:root{
  --blue:#2d5bff;
  --navy:#0c1930;
  --green:#14b87c;
  --purple:#8b5cf6;
  --red:#e5343a;
  --ink:#111418;
  --muted:#4a4f57;
  --footer:#1b1c1f;
  --white:#fff;
  --line:#cfd3da;
}
*{margin:0;padding:0;box-sizing:border-box}
html,body{width:1200px;height:3472px;overflow:hidden}
body{font-family:"Inter",Arial,sans-serif;color:var(--ink);background:var(--white);position:relative}
.abs{position:absolute}
.display{font-family:"Bebas Neue","Oswald",sans-serif;font-weight:400;letter-spacing:.5px;line-height:1}
.accent{color:var(--blue)}
.btn{position:absolute;display:flex;align-items:stretch;background:var(--blue);color:var(--white);font-size:11px;font-weight:700;text-transform:uppercase;letter-spacing:.2px}
.btn .label{flex:1;display:flex;align-items:center;justify-content:center}
.btn .arrow{width:38px;border-left:2px solid var(--white);display:flex;align-items:center;justify-content:center}
.btn.light{background:var(--white);color:var(--ink)}
.btn.light .arrow{border-left-color:var(--blue)}
.photo{position:absolute}

.nav{top:0;left:0;width:1200px;height:51px;background:var(--white)}
.brand{font-weight:700;font-size:21px;color:var(--ink);letter-spacing:-.3px;display:flex;align-items:center;gap:8px}
.brand .sq{width:12px;height:12px;background:var(--blue)}
.nav .links{left:491px;top:20px;display:flex;gap:27px;font-size:11px;font-weight:600}

.hero{top:51px;left:0;width:1200px;height:504px;background:linear-gradient(100deg,#1b2742 0%,#141f37 45%,#0e1a33 100%)}
.hero h1{position:absolute;left:121px;top:125px;font-size:86px;color:var(--white)}
.hero p{position:absolute;left:123px;top:296px;width:300px;font-size:10.5px;line-height:1.45;color:#e8ecf3}

.about h2{font-size:37px}
.about p{font-size:10px;line-height:1.6;color:var(--muted);width:345px;margin-bottom:16px}

.band{top:1202px;left:0;width:1200px;height:708px;background:var(--navy)}
.not-card{top:1135px;width:188px;height:137px;background:var(--white);border:1px solid var(--line);display:flex;flex-direction:column;align-items:center;padding-top:22px;text-align:center;font-size:14.5px;font-weight:500;line-height:1.25}
.not-card svg{margin-bottom:8px}

.pillar{top:1414px;width:469px;height:433px;background:var(--white)}
.pillar .img{height:235px}
.pillar h3{font-size:22px;margin:22px 0 0 17px}
.pillar .row{margin:8px 17px 0;width:345px;font-size:9.8px;line-height:1.6;color:var(--ink)}
.pillar .row b{font-size:14px;font-weight:600}
.pillar .out{position:absolute;left:0;bottom:0;width:100%;height:55px;background:var(--green);color:var(--white);font-size:9.5px;line-height:1.6;padding:12px 17px}
.pillar .out b{font-size:13.5px;font-weight:600}

.post{top:2516px;width:306px}
.post .frame{height:217px;background:var(--purple);padding:14px 0 0 14px}
.post .frame div{height:203px}
.post h4{font-size:14.5px;font-weight:500;line-height:1.25;margin-top:12px}
.post p{font-size:9.5px;line-height:1.4;color:var(--muted);margin-top:4px;width:240px}
.post a{position:absolute;top:314px;font-size:9.5px;color:var(--blue);text-decoration:underline}
.nav-arrow{top:2615px}

.cta{top:2975px;left:0;width:1200px;height:278px;background:var(--blue);color:var(--white);text-align:center}
.cta h2{font-size:84px;margin-top:58px;letter-spacing:1px}
.cta p{font-size:15px;margin-top:4px}

.footer{top:3253px;left:0;width:1200px;height:219px;background:var(--footer);color:#b5b8bf}
.footer h5{font-family:"Bebas Neue",sans-serif;font-weight:400;font-size:15px;letter-spacing:1.2px;color:var(--white)}
.footer .small{font-size:9px;line-height:1.75}
.footer .div{top:35px;width:1px;height:150px;background:#3a3b40}
.contact-row{display:flex;align-items:center;gap:12px;font-size:9.5px;margin-top:12px}
.ic{width:23px;height:23px;border:1.5px solid var(--white);border-radius:50%;display:flex;align-items:center;justify-content:center;flex:none}
</style>
</head>
<body>

<header class="nav abs">
  <div class="brand abs" style="left:121px;top:15px"><span>REACH CRAFTERS</span><span class="sq"></span></div>
  <nav class="links abs"><span>ABOUT US</span><span>SERVICES</span><span>INSIGHT</span></nav>
  <div class="btn" style="left:938px;top:8px;width:140px;height:34px"><span class="label">Contact us</span><span class="arrow"><svg width="12" height="12" viewBox="0 0 12 12"><path d="M1 6h10M7 2l4 4-4 4" stroke="#fff" stroke-width="1.3" fill="none"/></svg></span></div>
</header>

<section class="hero abs" role="img" aria-label="Dimmed photo of a business team meeting in an office">
  <h1 class="display">BE FOUND.<br><span style="display:inline-block;margin-top:4px">BE <span class="accent">CHOSEN.</span></span></h1>
  <p>Decision-grade marketing strategy for high-ticket service businesses that want predictable, scalable demand.</p>
  <div class="btn" style="left:121px;top:353px;width:214px;height:40px"><span class="label">Explore our approach</span><span class="arrow"><svg width="12" height="12" viewBox="0 0 12 12"><path d="M1 6h10M7 2l4 4-4 4" stroke="#fff" stroke-width="1.3" fill="none"/></svg></span></div>
  <div class="abs" style="left:543px;top:51px;width:8px;height:395px;background:var(--green)"></div>
  <div class="photo" role="img" aria-label="Photo of four colleagues discussing around a laptop" style="left:551px;top:51px;width:527px;height:395px;background:linear-gradient(160deg,#8a97a6 0%,#4e5a68 50%,#2a3341 100%)"></div>
</section>

<section class="about">
  <div class="abs" style="left:121px;top:617px;width:364px;height:399px;border:5px solid var(--green)"></div>
  <div class="photo" role="img" aria-label="Photo of a presenter in a suit speaking to colleagues" style="left:129px;top:625px;width:348px;height:383px;background:linear-gradient(150deg,#e6e9ee 0%,#aab3c0 50%,#4a5567 100%)"></div>
  <div class="photo" role="img" aria-label="Photo of a laptop showing analytics dashboards" style="left:348px;top:731px;width:265px;height:216px;background:linear-gradient(140deg,#6b5444 0%,#3a2e27 55%,#1c1a1a 100%)"></div>
  <h2 class="display abs" style="left:689px;top:676px">ABOUT REACH <span class="accent">CRAFTERS</span></h2>
  <div class="abs" style="left:689px;top:719px">
    <p>Reach Crafters is a playbook-as-a-service consultancy that teaches high-ticket service businesses to understand why qualified buyers don't choose them—and design buying experiences where reaching full commitment is the natural conclusion.</p>
    <p>We apply the tools of Choice Architecture and Buyer Insight to diagnose revenue problems and design solutions.</p>
    <p>The business model is a product company with consulting as a complementary premium tier.</p>
  </div>
  <div class="btn" style="left:690px;top:906px;width:203px;height:40px"><span class="label">Learn more about us</span><span class="arrow"><svg width="12" height="12" viewBox="0 0 12 12"><path d="M1 6h10M7 2l4 4-4 4" stroke="#fff" stroke-width="1.3" fill="none"/></svg></span></div>
</section>

<h2 class="display abs" style="left:0;top:1075px;width:1200px;text-align:center;font-size:36px">WHAT REACH <span class="accent">CRAFTERS</span> IS NOT</h2>
<div class="band abs"></div>
<div class="not-card abs" style="left:121px">
  <svg width="48" height="48" viewBox="0 0 48 48"><circle cx="24" cy="24" r="22" fill="var(--red)" stroke="#f3b3b5" stroke-width="3"/><path d="M16 16l16 16M32 16L16 32" stroke="#fff" stroke-width="5" stroke-linecap="round"/></svg>
  <span>A marketing<br>consultancy FPer se</span></div>
<div class="not-card abs" style="left:313px">
  <svg width="48" height="48" viewBox="0 0 48 48"><circle cx="24" cy="24" r="22" fill="var(--red)" stroke="#f3b3b5" stroke-width="3"/><path d="M16 16l16 16M32 16L16 32" stroke="#fff" stroke-width="5" stroke-linecap="round"/></svg>
  <span>A funnel Agency</span></div>
<div class="not-card abs" style="left:505px">
  <svg width="48" height="48" viewBox="0 0 48 48"><circle cx="24" cy="24" r="22" fill="var(--red)" stroke="#f3b3b5" stroke-width="3"/><path d="M16 16l16 16M32 16L16 32" stroke="#fff" stroke-width="5" stroke-linecap="round"/></svg>
  <span>A sales<br>Enablement Firm</span></div>
<div class="not-card abs" style="left:697px">
  <svg width="48" height="48" viewBox="0 0 48 48"><circle cx="24" cy="24" r="22" fill="var(--red)" stroke="#f3b3b5" stroke-width="3"/><path d="M16 16l16 16M32 16L16 32" stroke="#fff" stroke-width="5" stroke-linecap="round"/></svg>
  <span>An<br>Execution Partner</span></div>
<div class="not-card abs" style="left:889px">
  <svg width="48" height="48" viewBox="0 0 48 48"><circle cx="24" cy="24" r="22" fill="var(--red)" stroke="#f3b3b5" stroke-width="3"/><path d="M16 16l16 16M32 16L16 32" stroke="#fff" stroke-width="5" stroke-linecap="round"/></svg>
  <span>A time-for<br>Money Advisory</span></div>

<h2 class="display abs" style="left:0;top:1331px;width:1200px;text-align:center;font-size:36px;color:var(--white)">THE TWO <span class="accent">PILLARS</span></h2>
<p class="abs" style="left:0;top:1373px;width:1200px;text-align:center;font-size:11px;color:var(--white)">Reach Crafters' methodology rests on two complementary disciplines:</p>

<article class="pillar abs" style="left:121px">
  <div class="img" role="img" aria-label="Photo of a man reviewing charts on a tablet and laptop" style="background:linear-gradient(130deg,#c9a77a 0%,#7a5a3c 50%,#2a2522 100%)"></div>
  <h3 class="display">BUYER INSIGHT</h3>
  <div class="row"><b>Definition:</b> The discipline of discovering and diagnosing what's actually happening in a buyer's journey—before prescribing solutions.</div>
  <div class="row"><b>Metaphor:</b> Reconnaissance. Gathering intel on the battlefield before making strategic decisions.</div>
  <div class="out"><b>Output:</b> A dossier—a clear-eyed assessment of reality,<br>not assumptions</div>
</article>
<article class="pillar abs" style="left:609px">
  <div class="img" role="img" aria-label="Photo of wooden letter blocks, a keyboard and printed infographics" style="background:linear-gradient(130deg,#d8d6d2 0%,#bdb6aa 50%,#8f8474 100%)"></div>
  <h3 class="display">CHOICE ARCHITECTURE</h3>
  <div class="row"><b>Definition:</b> The discipline of applying behavioral science principles to design buying experiences where saying yes feels safer than saying no.</div>
  <div class="row"><b>Metaphor:</b> Decision architecture. Engineering the environment in which high-stakes choices get made.</div>
  <div class="out"><b>Output:</b> A design system—principles and architecture for what to<br>build, not just tactics to try.</div>
</article>

<div class="abs" style="left:195px;top:1966px;width:808px;height:381px;background:var(--blue)"></div>
<div class="abs" role="img" aria-label="Explainer video still of business people reviewing a laptop" style="left:245px;top:2017px;width:708px;height:381px;background:linear-gradient(180deg,#8d929a 0%,#555a62 55%,#1f2226 100%)">
  <svg class="abs" style="left:327px;top:158px" width="56" height="56" viewBox="0 0 56 56"><circle cx="28" cy="28" r="26" fill="#fff" stroke="rgba(0,0,0,.25)" stroke-width="4"/><path d="M23 18l15 10-15 10z" fill="var(--blue)"/></svg>
</div>

<h2 class="display abs" style="left:0;top:2457px;width:1200px;text-align:center;font-size:36px">LATEST <span class="accent">BLOG</span></h2>
<svg class="abs nav-arrow" style="left:87px" width="16" height="16" viewBox="0 0 16 16"><circle cx="8" cy="8" r="7" fill="none" stroke="#222"/><path d="M11 8H5M7.5 5.5L5 8l2.5 2.5" stroke="#222" fill="none"/></svg>
<svg class="abs nav-arrow" style="left:1096px" width="16" height="16" viewBox="0 0 16 16"><circle cx="8" cy="8" r="7" fill="none" stroke="#222"/><path d="M5 8h6M8.5 5.5L11 8l-2.5 2.5" stroke="#222" fill="none"/></svg>

<article class="post abs" style="left:121px">
  <div class="frame"><div role="img" aria-label="Photo of wooden figures in a line with a red figure and arrow" style="background:linear-gradient(135deg,#9fd6de 0%,#6bbec9 100%)"></div></div>
  <h4>Demand Is Not Leads</h4>
  <p>Why most high-ticket service businesses chase activity instead of real demand—and how that mistake limits growth.</p>
  <a>LEARN MORE</a>
</article>
<article class="post abs" style="left:446px">
  <div class="frame"><div role="img" aria-label="Photo of two men discussing a chart at a desk" style="background:linear-gradient(135deg,#9a8a78 0%,#5e5248 100%)"></div></div>
  <h4>Why Most Marketing Advice<br>Fails Service Businesses</h4>
  <p>What works in ecommerce and SaaS often breaks in high-consideration, high-trust sales environments.</p>
  <a>LEARN MORE</a>
</article>
<article class="post abs" style="left:771px">
  <div class="frame"><div role="img" aria-label="Photo of two men reviewing a tablet together" style="background:linear-gradient(135deg,#b59a7c 0%,#5a4a3e 100%)"></div></div>
  <h4>How Buyers Actually Choose<br>Service Providers</h4>
  <p>A clearer mental model for understanding buyer decisions in complex, competitive markets.</p>
  <a>LEARN MORE</a>
</article>

<div class="abs display" style="left:0;top:2882px;width:1200px;text-align:center;font-size:118px;color:#f2f3f6;letter-spacing:6px">REACH CRAFTERS</div>
<div class="btn" style="left:515px;top:2886px;width:170px;height:40px"><span class="label">View all blog</span><span class="arrow"><svg width="12" height="12" viewBox="0 0 12 12"><path d="M1 6h10M7 2l4 4-4 4" stroke="#fff" stroke-width="1.3" fill="none"/></svg></span></div>

<section class="cta abs">
  <h2 class="display">READY TO STOP GUESSING?</h2>
  <p>If you're serious about building predictable demand, let's talk.</p>
  <div class="btn light" style="left:495px;top:174px;width:209px;height:40px"><span class="label">Contact Reach Crafters</span><span class="arrow"><svg width="12" height="12" viewBox="0 0 12 12"><path d="M1 6h10M7 2l4 4-4 4" stroke="#2d5bff" stroke-width="1.3" fill="none"/></svg></span></div>
</section>

<footer class="footer abs">
  <div class="abs" style="left:121px;top:37px;width:198px;height:36px;background:var(--white);display:flex;align-items:center;justify-content:center;font-weight:700;font-size:18px;color:var(--ink)">REACH CRAFTERS</div>
  <p class="abs small" style="left:121px;top:87px;width:245px">Reach Crafters is a playbook-as-a-service consultancy that teaches high-ticket service businesses to understand why qualified buyers don't choose them—and design buying experiences where reaching full commitment is the natural conclusion.</p>
  <div class="abs div" style="left:386px"></div>
  <div class="abs" style="left:437px;top:40px">
    <h5>MAIN LINKS</h5>
    <div class="small" style="margin-top:12px;line-height:2.4">About us<br>Services<br>Insights<br>Contact Us.</div>
  </div>
  <div class="abs div" style="left:605px"></div>
  <div class="abs" style="left:657px;top:40px">
    <h5>CONTACT US</h5>
    <div class="contact-row" style="margin-top:14px"><span class="ic"><svg width="11" height="11" viewBox="0 0 24 24"><path d="M6.6 10.8a15 15 0 006.6 6.6l2.2-2.2c.3-.3.7-.4 1-.2 1.1.4 2.3.6 3.6.6.6 0 1 .4 1 1V20c0 .6-.4 1-1 1A17 17 0 013 4c0-.6.4-1 1-1h3.5c.6 0 1 .4 1 1 0 1.3.2 2.5.6 3.6.1.3 0 .7-.2 1z" fill="#fff"/></svg></span>1-800-555-0142</div>
    <div class="contact-row"><span class="ic"><svg width="11" height="9" viewBox="0 0 22 16"><rect x="1" y="1" width="20" height="14" rx="1" fill="#fff"/><path d="M1 1l10 8 10-8" stroke="#1b1c1f" stroke-width="1.6" fill="none"/></svg></span><span style="color:var(--blue)">hello@reachcrafters.co</span></div>
  </div>
  <div class="abs div" style="left:876px"></div>
  <div class="abs" style="left:959px;top:40px">
    <h5>FOLLOW US</h5>
    <div class="contact-row" style="margin-top:14px"><span class="ic"></span>Friendnet</div>
    <div class="contact-row"><span class="ic"></span>Chirpline</div>
    <div class="contact-row"><span class="ic"></span>Workgrid</div>
  </div>
  <div class="abs" style="left:0;top:197px;width:1200px;text-align:center;font-size:8.5px">© Copyright 2026 Reach Crafters All Rights Reserved.</div>
</footer>

</body>
</html>
```